Business Cards Design for the electrical wholesaler: clean bold dynamic :)

We need a business card design that would follow our latest brand guidelines. As an electrical wholesaler we want to bring a fresh look and feel into the industry. The design should be clean bold and dynamic. It should come alive with the renewed energy of our green colour. Our grey colour should keep things balanced and complement the notion of maturity and responsibility. We employ Lato as a corporate font however are not bound by this font and we’re open to interpretation here.

Target Market(s)

Electrical contractors

Industry/Entity Type

Business

Contact Information for Business Card

Logo
Name & Surname: Halyna Dorosh
Job Title: Director of Marketing
Email: halya.dorosh@quillmail.example
Cell phone: XXX.XXX.XXXX
Address: 20517 - 87 Ave. Edmonton, AB, Canada. T6K 4N8
Business Phone: 780.555.0184
Website: www.brovix.example

Font styles to use
Other font styles liked:
• Lato

Requirements
Must have
• Logo & website
Nice to have
• Brand elements - some of them you may find in the attached Brand Guidelines (e.g. three lines on the background signifying "W")

```html
<!DOCTYPE html>
<html lang="en">
<head>
<meta charset="utf-8">
<title>Brovix Business Card</title>
<link href="https://fonts.googleapis.com/css2?family=Lato:wght@400;700&display=swap" rel="stylesheet">
<style>
  :root {
    --backdrop: #a4a4a4;
    --card-light: #ececec;
    --card-dark: #4a4e51;
    --brand-grey: #4d4f52;
    --brand-green: #8dc63f;
    --text-grey: #3f4144;
    --rule: #8a8a8a;
    --white: #ffffff;
  }
  html, body {
    margin: 0;
    padding: 0;
    width: 1200px;
    height: 900px;
    overflow: hidden;
    background: var(--backdrop);
    font-family: "Lato", sans-serif;
  }
  .canvas {
    position: relative;
    width: 1200px;
    height: 900px;
  }
  .card {
    position: absolute;
    top: 170px;
    width: 347px;
    height: 561px;
    box-sizing: border-box;
  }
  .card-front {
    left: 259px;
    background: var(--card-light);
    text-align: center;
    color: var(--text-grey);
  }
  .card-back {
    left: 631px;
    background: var(--card-dark);
  }
  .brand-name {
    position: absolute;
    left: 0;
    right: 0;
    top: 155px;
    margin: 0;
    font-size: 76px;
    font-weight: 400;
    line-height: 1;
    color: var(--brand-grey);
    letter-spacing: -1px;
  }
  .brand-tagline {
    position: absolute;
    left: 0;
    right: 0;
    top: 250px;
    margin: 0;
    font-size: 12.5px;
    font-weight: 700;
    letter-spacing: 1.6px;
    color: var(--brand-grey);
  }
  .person {
    position: absolute;
    left: 0;
    right: 0;
    top: 318px;
  }
  .person-name {
    margin: 0;
    font-size: 26px;
    font-weight: 400;
    color: var(--brand-green);
    line-height: 1.2;
  }
  .person-title {
    margin: 2px 0 0;
    font-size: 15.5px;
    line-height: 1.2;
  }
  .rule {
    width: 163px;
    height: 1px;
    background: var(--rule);
    margin: 0 auto;
    border: 0;
  }
  .rule-top { position: absolute; left: 92px; top: 376px; }
  .rule-bottom { position: absolute; left: 92px; top: 473px; }
  .contact-list {
    position: absolute;
    left: 0;
    right: 0;
    top: 384px;
    margin: 0;
    padding: 0;
    list-style: none;
    font-size: 15px;
    line-height: 20px;
  }
  .contact-label {
    color: var(--brand-green);
    font-weight: 700;
  }
  .contact-web {
    color: var(--brand-green);
    font-weight: 700;
  }
  .address {
    position: absolute;
    left: 0;
    right: 0;
    top: 482px;
    margin: 0;
    font-style: normal;
    font-size: 15px;
    line-height: 21px;
  }
  .back-brand {
    position: absolute;
    left: 32px;
    top: 458px;
    margin: 0;
    font-size: 64px;
    font-weight: 400;
    line-height: 1;
    color: var(--white);
    letter-spacing: -1px;
  }
</style>
</head>
<body>
<main class="canvas">
  <section class="card card-front" aria-label="Business card front">
    <h1 class="brand-name">brovix</h1>
    <p class="brand-tagline">ELECTRICAL WHOLESALERS</p>

    <div class="person">
      <h2 class="person-name">Halyna Dorosh</h2>
      <p class="person-title">Managing Director</p>
    </div>

    <hr class="rule rule-top">
    <ul class="contact-list">
      <li><span class="contact-label">P:</span> 044-123 456 789</li>
      <li><span class="contact-label">M:</span> 044-123 456 789</li>
      <li><span class="contact-label">E:</span> info@brovix.example</li>
      <li class="contact-web">www.brovix.example</li>
    </ul>
    <hr class="rule rule-bottom">

    <address class="address">12345, Address Goes Here<br>Country Name, 123456.</address>
  </section>

  <section class="card card-back" aria-label="Business card back">
    <p class="back-brand">brovix</p>
  </section>
</main>
</body>
</html>
```